Profesional personal website needs design and business card

I need a business card with my professional name as a logo "Dorian Vitality" for my business. I am a Wellness Coach, consultant and trainer. So it should be professional, wellness oriented and modern.

Target Market(s)

Private clients, governments, corporations. Luxury and high market.

Industry/Entity Type

Health And Wellness

Contact Information for Business Card

Dorian Vitality should be the logo

Colors

Designer to choose colors to be used in the design.

Requirements
Must have
• Dorian Vitality
• Name: Tomás Lirandel
• Wellness Coach, Consultant & Trainer.
• Website: www.dorianvitality-example.com
• Phone:
• Spain (+34) 612 480 317
• (USA) +1 (555) 610 4829
Nice to have
• The most important is the design of "Dorian Vitality", as this is going to be my personal brand logo. It should be professional, wellness, high end and actual.
Should not have
• no golds, no baroque style..

```html
<!DOCTYPE html>
<html lang="en">
<head>
<meta charset="utf-8">
<title>Dorian Vitality — Business Card</title>
<link rel="stylesheet" href="https://fonts.googleapis.com/css2?family=Montserrat:wght@400;500;700&display=swap">
<style>
  :root {
    --bg: #d9d9dc;
    --charcoal: #252528;
    --green: #8bc541;
    --white: #ffffff;
  }
  * { margin: 0; padding: 0; box-sizing: border-box; }
  html, body {
    width: 1200px; height: 1200px; overflow: hidden;
    background: var(--bg);
    font-family: "Montserrat", sans-serif;
  }
  .sheet {
    width: 1200px; height: 1200px;
    display: flex; flex-direction: column;
    align-items: center; justify-content: center;
    gap: 40px;
  }
  .card {
    width: 840px; height: 537px;
    display: block;
    box-shadow: 0 10px 30px rgba(0,0,0,0.18);
  }
  .card text { font-family: "Montserrat", sans-serif; white-space: pre; }
</style>
</head>
<body>
<main class="sheet">

  <!-- Card back: brand name -->
  <svg class="card card-back" viewBox="0 0 966 618" xmlns="http://www.w3.org/2000/svg">
    <rect class="card-back__base" width="966" height="618" fill="var(--charcoal)"/>
    <circle class="brand__ring" cx="196" cy="309" r="26" fill="none" stroke="var(--green)" stroke-width="5"/>
    <text class="brand__name" x="244" y="325" font-size="48" font-weight="500"
          fill="var(--green)" letter-spacing="2">Dorian Vitality</text>
  </svg>

  <!-- Card front: contact details -->
  <svg class="card card-front" viewBox="0 0 966 618" xmlns="http://www.w3.org/2000/svg">
    <rect class="card-front__base" width="966" height="618" fill="var(--green)"/>
    <rect class="card-front__top-band" width="966" height="32" fill="var(--charcoal)"/>

    <text class="holder__name" x="60" y="98" font-size="40" fill="var(--white)" letter-spacing="3">
      <tspan font-weight="700">TOMÁS</tspan><tspan font-weight="400"> LIRANDEL</tspan>
    </text>
    <text class="holder__role" x="62" y="125" font-size="15.5" font-weight="500"
          fill="var(--white)" letter-spacing="2.6">Wellness Coach - Consultant &amp; Trainer</text>
    <rect class="holder__rule" x="0" y="150" width="486" height="4" fill="var(--charcoal)"/>

    <path class="icon-cursor" d="M62 172 L62 196 L68 190 L73 200 L77 198 L72 188 L80 188 Z" fill="var(--white)"/>
    <text class="holder__web" x="110" y="196" font-size="25" font-weight="400"
          fill="var(--white)" letter-spacing="1.2">www.dorianvitality-example.com</text>

    <!-- contact band -->
    <rect class="contact-band" x="560" y="456" width="406" height="162" fill="var(--charcoal)"/>

    <path class="icon-phone" d="M598 525 q3 -4 7 -2 l4 5 q1 3 -2 5 q3 6 9 9 q2 -3 5 -2 l5 4 q2 4 -2 7 q-4 3 -9 1 q-12 -6 -18 -18 q-2 -5 1 -9 Z" fill="var(--white)"/>
    <text class="holder__phone" x="642" y="524" font-size="22" font-weight="400" fill="var(--white)" letter-spacing="0.6">SPAIN(+34) 612 480 317</text>
    <text class="holder__phone" x="642" y="554" font-size="22" font-weight="400" fill="var(--white)" letter-spacing="0.6">USA  +1 (555) 610 4829</text>
  </svg>

</main>
</body>
</html>
```